Business Card Design

We need a design for business cards for our company. We have a logo. We teach EMT's and we are based out of Virginia. The information that will need to add would be, name, title, phone number, email, address. On the back of the business card would be "We help you, help others"

Target Market(s)

People that want to become EMT's

Colors

Designer to choose colors to be used in the design.

Requirements
Must have
• company logo

```html
<!DOCTYPE html>
<html lang="en">
<head>
<meta charset="utf-8">
<title>Vantrel Care Academy – Business Card</title>
<link rel="stylesheet" href="https://fonts.googleapis.com/css2?family=Open+Sans:wght@400;700&display=swap">
<style>
  :root {
    --navy: #212a35;
    --slate: #6e7b86;
    --red: #ee2c4a;
    --white: #ffffff;
  }
  html, body {
    margin: 0;
    padding: 0;
    width: 1200px;
    height: 686px;
    overflow: hidden;
    background: var(--navy);
  }
  .card {
    position: relative;
    width: 1200px;
    height: 686px;
    overflow: hidden;
    background: var(--navy);
    font-family: "Open Sans", sans-serif;
    color: var(--white);
  }
  .card__shapes {
    position: absolute;
    inset: 0;
  }
  .brand {
    position: absolute;
    left: 50px;
    top: 292px;
    width: 570px;
    display: flex;
    align-items: center;
    gap: 18px;
  }
  .brand__dot {
    width: 24px;
    height: 24px;
    border-radius: 50%;
    background: var(--red);
    flex: none;
  }
  .brand__name {
    margin: 0;
    font-weight: 700;
    font-size: 40px;
    line-height: 48px;
    letter-spacing: 1px;
    text-transform: uppercase;
    color: var(--red);
  }
  .person {
    position: absolute;
    left: 790px;
    top: 177px;
    height: 86px;
    padding-left: 12px;
    border-left: 12px solid var(--white);
  }
  .person__name {
    margin: 0;
    font-weight: 400;
    font-size: 41px;
    line-height: 46px;
    margin-top: -6px;
  }
  .person__title {
    margin: 0;
    font-weight: 400;
    font-size: 35px;
    line-height: 44px;
  }
  .contacts {
    position: absolute;
    left: 769px;
    top: 302px;
    margin: 0;
    padding: 0;
    list-style: none;
    font-size: 28px;
    line-height: 38px;
  }
  .contacts__item {
    display: flex;
    align-items: flex-start;
    gap: 23px;
    margin-bottom: 14px;
  }
  .contacts__icon {
    width: 26px;
    height: 26px;
    margin-top: 6px;
    flex: none;
    fill: var(--white);
  }
</style>
</head>
<body>
  <main class="card">
    <svg class="card__shapes" width="1200" height="686" viewBox="0 0 1200 686" aria-hidden="true">
      <polygon points="561,0 767,0 703,206" fill="var(--slate)"/>
      <polygon points="591,489 608,506 758,686 527,686" fill="var(--slate)"/>
      <polygon points="767,0 1200,0 1200,686 758,686 608,506" fill="var(--red)"/>
    </svg>

    <div class="brand">
      <span class="brand__dot"></span>
      <p class="brand__name">Vantrel Care<br>Academy</p>
    </div>

    <header class="person">
      <h1 class="person__name">Daniel Hart</h1>
      <p class="person__title">Director</p>
    </header>

    <ul class="contacts">
      <li class="contacts__item">
        <svg class="contacts__icon" viewBox="0 0 24 24" aria-hidden="true"><rect x="6" y="1" width="12" height="22" rx="2.5"/><rect x="8.5" y="4" width="7" height="13" fill="var(--red)"/><circle cx="12" cy="20" r="1.2" fill="var(--red)"/></svg>
        <span>0522 44 67890</span>
      </li>
      <li class="contacts__item">
        <svg class="contacts__icon" viewBox="0 0 24 24" aria-hidden="true"><rect x="1" y="5" width="22" height="14" rx="1"/><polyline points="2,6 12,13 22,6" fill="none" stroke="var(--red)" stroke-width="1.8"/></svg>
        <span>Info@vantrelcare.com</span>
      </li>
      <li class="contacts__item">
        <svg class="contacts__icon" viewBox="0 0 24 24" aria-hidden="true"><circle cx="12" cy="12" r="10"/><rect x="2" y="10" width="20" height="4" fill="var(--red)"/></svg>
        <span>www.vantrelcare.com</span>
      </li>
      <li class="contacts__item">
        <svg class="contacts__icon" viewBox="0 0 24 24" aria-hidden="true"><path d="M12 1a6 6 0 0 0-6 6c0 4.5 6 10 6 10s6-5.5 6-10a6 6 0 0 0-6-6zm0 8.5a2.5 2.5 0 1 1 0-5 2.5 2.5 0 0 1 0 5z"/><path d="M2 23l3-7h3l-1 1.8H6.2L4.8 21h14.4l-1.4-3.2H17L16 16h3l3 7z"/></svg>
        <span>2204/56 harbour street,<br>brisbane qld 4000</span>
      </li>
    </ul>
  </main>
</body>
</html>
```